PYLON SIGN FOR “MEADOWLARK CAR WASH SPRINT”

please see the new images in my brief. I have a logo design and the colors I would like you to follow.

please put "meadowlark car wash sprint" in the logo

Target Market(s)

GENERAL PUBLIC

Industry/Entity Type

CAR WASH

Font styles to use
Other font styles liked:
• CURSIVE AND BLOCK LETTERING BOTH AS IN THE SAMPLE PIC

Colors
00AB8E
00BBA5
67D7C9
C6EFE9
E9F9F6
6B429C
8869AF
B7A5CE
E3DAEB
F3F0F8

Requirements
Must have
• 1. “MEADOWLARK CAR WASH SPRINT” PLEASE PUT THIS IN THE LOGO 2. USE BLACK, WHITE, GREEN AND SILVER FOR A COLOR
Nice to have
• I WOULD LIKE TO SEE THE SIGN IN BOTH COLOR THEMES: WHITE, BLACK, GREEN AND SILVER AND WHITE BLACK PURPLE AND SILVER

```html
<!DOCTYPE html>
<html lang="en">
<head>
<meta charset="utf-8">
<title>Meadowlark Car Wash Sprint – Pylon Sign</title>
<link href="https://fonts.googleapis.com/css2?family=Russo+One&family=Michroma&display=swap" rel="stylesheet">
<style>
  :root {
    --page-bg: #4d4d4d;
    --sign-black: #050806;
    --sign-deep: #0e1f12;
    --sign-green: #3f7a1f;
    --lime: #8cc63f;
    --lime-bright: #a6d843;
    --lime-dark: #4f8f1e;
    --silver-light: #ffffff;
    --silver-mid: #c9c9c9;
    --silver-dark: #8a8a8a;
  }
  * { margin: 0; padding: 0; box-sizing: border-box; }
  html, body {
    width: 1200px;
    height: 2929px;
    overflow: hidden;
    background: var(--page-bg);
  }
  .canvas {
    position: relative;
    width: 1200px;
    height: 2929px;
    display: flex;
    align-items: center;
    justify-content: center;
  }
  .pylon-sign {
    position: relative;
    width: 1040px;
    height: 1300px;
    overflow: hidden;
    background:
      radial-gradient(ellipse 55% 35% at 0% 0%, var(--lime) 0%, rgba(140,198,63,0) 100%),
      radial-gradient(ellipse 60% 45% at 100% 100%, var(--sign-green) 0%, rgba(63,122,31,0) 100%),
      linear-gradient(180deg, var(--sign-black) 0%, var(--sign-black) 45%, var(--sign-deep) 100%);
    box-shadow: 0 20px 40px rgba(0,0,0,0.55);
  }
  .brand-mark {
    position: absolute;
    top: 235px;
    left: 0;
    width: 100%;
    display: flex;
    align-items: center;
    justify-content: center;
    gap: 18px;
  }
  .brand-mark__dot {
    width: 26px;
    height: 26px;
    border-radius: 50%;
    background: var(--lime);
  }
  .brand-mark__name {
    font-family: "Russo One", sans-serif;
    font-size: 40px;
    letter-spacing: 1px;
    color: var(--lime);
  }
  .headline {
    position: absolute;
    top: 430px;
    left: 0;
    width: 100%;
    text-align: center;
  }
  .headline__name {
    display: block;
    font-family: "Russo One", sans-serif;
    font-size: 128px;
    line-height: 1;
    color: var(--lime);
    background: linear-gradient(180deg, var(--lime-bright) 0%, var(--lime-bright) 50%, var(--lime-dark) 52%, var(--lime) 100%);
    -webkit-background-clip: text;
    background-clip: text;
    -webkit-text-fill-color: transparent;
    filter: drop-shadow(0 0 10px rgba(166,216,67,0.45));
  }
  .headline__service,
  .headline__tag {
    display: block;
    font-family: "Michroma", sans-serif;
    font-weight: 400;
    line-height: 1.05;
    transform: skewX(-12deg);
    background: linear-gradient(180deg, var(--silver-light) 0%, var(--silver-mid) 48%, var(--silver-dark) 52%, var(--silver-light) 100%);
    -webkit-background-clip: text;
    background-clip: text;
    -webkit-text-fill-color: transparent;
    filter: drop-shadow(0 0 8px rgba(255,255,255,0.35));
  }
  .headline__service {
    margin-top: 22px;
    font-size: 84px;
  }
  .headline__tag {
    margin-top: 4px;
    font-size: 84px;
  }
  .car-illustration {
    position: absolute;
    left: 50%;
    bottom: 0;
    width: 520px;
    height: 430px;
    transform: translateX(-50%);
    border-radius: 240px 240px 0 0;
    background: radial-gradient(ellipse at 50% 40%, var(--lime-bright) 0%, var(--lime) 45%, var(--lime-dark) 100%);
    border: 10px solid var(--silver-dark);
    border-bottom: none;
  }
</style>
</head>
<body>
  <main class="canvas">
    <section class="pylon-sign">
      <div class="brand-mark">
        <span class="brand-mark__dot"></span>
        <span class="brand-mark__name">MEADOWLARK CAR WASH SPRINT</span>
      </div>
      <h1 class="headline">
        <span class="headline__name">MEADOWLARK</span>
        <span class="headline__service">CAR WASH</span>
        <span class="headline__tag">SPRINT</span>
      </h1>
      <div class="car-illustration" role="img" aria-label="Illustration of a green car front surrounded by soap foam and bubbles"></div>
    </section>
  </main>
</body>
</html>
```